International Travel & Visas Firm needs a Schengen Visa eBook Cover Design

We need an ebook cover design for an online based travel, immigration, visas & nationality law firm called 'OrV' (orbit and voyage). We are all about helping people overcome the obstacles to travel and ensuring that people achieve their dreams and ambitions through travel to various destinations and bettering their lives.This initial ebook cover is for our downloaded pdf ebook all about Schengen visas and travelling to any of the 26 European countries that form the Schengen Zone.We want people to be excited about buying this book even before receiving it.We would like to see amazing designs that also speak to our logo and new branding.Check out https://orbitandvoyage.example/schengen-visas/ and http://orbitandvoyage.pages.funnelbox.example/start-your-schengen-visa-application

Target Market(s)

Travellers that want to get a visa to travel around Europe

Industry/Entity Type

Travel Industry

Colors
fbee3d
faa54b

Requirements
Must have
• - Title:
• Schengen Visa Guide
Nice to have
• - tagline:
• Liberate yourself and travel to 26 European Countries
• - OrV Logo
• - Reference to it being an insider's guide to Schengen Visas
• - a play on the word OrV (I am)

```html
<!DOCTYPE html>
<html lang="en">
<head>
<meta charset="UTF-8">
<title>Schengen Visa Guide – eBook Cover</title>
<link rel="stylesheet" href="https://fonts.googleapis.com/css2?family=Oswald:wght@500;700&display=swap">
<style>
  :root {
    --page-bg: #f2f2f2;
    --sky-top: #bfe5fa;
    --sky-bottom: #a9d8f5;
    --ground: #5ba6e4;
    --ground-light: #7bbcec;
    --art-deep: #3d8fd8;
    --art-warm: #f0b43c;
    --art-orange: #c9651c;
    --ink: #121212;
    --title-shadow: rgba(0, 0, 0, 0.35);
  }
  * { box-sizing: border-box; margin: 0; padding: 0; }
  html, body {
    width: 1200px;
    height: 800px;
    overflow: hidden;
    background: var(--page-bg);
  }
  .canvas {
    position: relative;
    width: 1200px;
    height: 800px;
  }
  .cover {
    position: absolute;
    left: 350px;
    top: 25px;
    width: 500px;
    height: 750px;
    overflow: hidden;
    background: linear-gradient(180deg, var(--sky-top) 0%, var(--sky-bottom) 100%);
    font-family: "Oswald", sans-serif;
    color: var(--ink);
    text-align: center;
  }
  .cover__tagline {
    position: absolute;
    top: 34px;
    left: 30px;
    right: 30px;
    font-weight: 500;
    font-size: 16px;
    line-height: 23px;
    letter-spacing: 1.3px;
    text-transform: uppercase;
  }
  .cover__title {
    position: absolute;
    top: 112px;
    left: 0;
    right: 0;
    font-weight: 700;
    font-size: 78px;
    line-height: 88px;
    letter-spacing: 4px;
    text-transform: uppercase;
    text-shadow: 3px 3px 0 var(--title-shadow);
  }
  .cover__art {
    position: absolute;
    left: 70px;
    top: 352px;
    width: 370px;
    height: 335px;
  }
  .cover__ground {
    position: absolute;
    left: 0;
    bottom: 0;
    width: 500px;
    height: 90px;
  }
  .cover__author {
    position: absolute;
    left: 0;
    right: 0;
    top: 696px;
    font-weight: 700;
    font-size: 25px;
    letter-spacing: 5px;
    text-transform: uppercase;
  }
</style>
</head>
<body>
  <main class="canvas">
    <section class="cover">
      <p class="cover__tagline">Liberate yourself and travel to 26 European countries</p>
      <h1 class="cover__title">Schengen<br>Visa Guide</h1>

      <svg class="cover__ground" viewBox="0 0 500 90" aria-hidden="true">
        <path d="M0 40 Q250 -10 500 40 L500 90 L0 90 Z" fill="var(--ground)"/>
      </svg>

      <svg class="cover__art" viewBox="0 0 370 335" role="img"
           aria-label="Travel illustration: suitcases with passport, map, camera and sun hat in front of a blue globe, planes flying around, European landmark skyline below">
        <defs>
          <linearGradient id="artFill" x1="0" y1="0" x2="1" y2="1">
            <stop offset="0" stop-color="var(--art-deep)"/>
            <stop offset="0.55" stop-color="var(--ground-light)"/>
            <stop offset="1" stop-color="var(--art-warm)"/>
          </linearGradient>
        </defs>
        <rect x="0" y="0" width="370" height="335" rx="24" fill="url(#artFill)" opacity="0.55"/>
      </svg>

      <p class="cover__author">Author Name</p>
    </section>
  </main>
</body>
</html>
```